business card

Business card for new business.
Red and black corporate colors.
Card can have an Indsutrial feel to it. Feel free to add Rust, Bolted steel, or graphics as you see fit. We provide highly specialized services to the below mentioned industries.
Keep information out of corners so that if I want I can choose rounded corners.
Information
- front. name - title - phone - email
- Rear
Refining - Rail - Infrastructure - Mining - Energy
Calgary - Edmonton - Fort McMurray - Revelstoke - Vancouver

```html
<!DOCTYPE html>
<html lang="en">
<head>
<meta charset="utf-8">
<title>Girderworks business card</title>
<link href="https://fonts.googleapis.com/css2?family=Open+Sans:wght@400;600;700;800&display=swap" rel="stylesheet">
<style>
  :root {
    --backdrop: #e6e6e6;
    --charcoal: #1f2225;
    --charcoal-edge: #2b2f33;
    --paper: #f7f7f7;
    --red: #e5151f;
    --steel: #7a7a7a;
    --white: #ffffff;
    --title-grey: #8a8a8a;
  }
  * { box-sizing: border-box; margin: 0; padding: 0; }
  html, body {
    width: 1200px; height: 900px; overflow: hidden;
    background: var(--backdrop);
    font-family: "Open Sans", Arial, sans-serif;
  }
  .canvas {
    width: 1200px; height: 900px;
    display: flex; flex-direction: column;
    align-items: center; justify-content: center; gap: 48px;
  }
  .card {
    width: 630px; height: 360px;
    position: relative;
    box-shadow: 0 10px 24px rgba(0,0,0,.22);
    display: flex; flex-direction: column; align-items: center;
  }
  /* Back side */
  .card--back {
    background: linear-gradient(135deg, var(--charcoal-edge), var(--charcoal));
    justify-content: center; gap: 30px;
  }
  .wordmark {
    display: flex; align-items: center; gap: 14px;
  }
  .wordmark__square {
    width: 22px; height: 22px; background: var(--red);
  }
  .wordmark__name {
    font-weight: 800; font-size: 50px; letter-spacing: 1px;
    color: var(--steel); line-height: 1;
  }
  .sectors {
    text-align: center; color: var(--white);
    font-size: 16px; line-height: 1.5; font-weight: 400;
  }
  .sectors .dot { color: var(--red); padding: 0 4px; }

  /* Front side */
  .card--front {
    background: var(--paper);
    padding-top: 84px;
  }
  .person { margin-top: 40px; text-align: center; }
  .person__name {
    color: var(--red); font-weight: 700; font-size: 20px; letter-spacing: .5px;
    text-transform: uppercase;
  }
  .person__title {
    color: var(--title-grey); font-size: 14px; letter-spacing: .5px;
    text-transform: uppercase; margin-top: 2px;
  }
  .contact-band {
    position: absolute; left: 0; right: 0; bottom: 0; height: 62px;
    background: var(--red);
    display: flex; align-items: center; justify-content: center; gap: 26px;
    color: var(--white); font-size: 15px;
  }
  .contact-item { display: flex; align-items: center; gap: 7px; }
  .contact-item svg { width: 16px; height: 16px; fill: var(--white); }
</style>
</head>
<body>
<main class="canvas">
  <section class="card card--back" aria-label="Card back">
    <div class="wordmark">
      <span class="wordmark__square"></span>
      <span class="wordmark__name">GIRDERWORKS</span>
    </div>
    <p class="sectors">
      Refining<span class="dot">•</span>Rail<span class="dot">•</span>Infrastructure<span class="dot">•</span>Mining<br>
      Energy<span class="dot">•</span>Calgary<span class="dot">•</span>Edmonton<span class="dot">•</span>Fort McMurray<br>
      Revelstoke<span class="dot">•</span>Vancouver
    </p>
  </section>

  <section class="card card--front" aria-label="Card front">
    <div class="wordmark">
      <span class="wordmark__square"></span>
      <span class="wordmark__name">GIRDERWORKS</span>
    </div>
    <div class="person">
      <p class="person__name">Mark Ellison</p>
      <p class="person__title">President</p>
    </div>
    <div class="contact-band">
      <span class="contact-item">
        <svg viewBox="0 0 24 24" aria-hidden="true"><path d="M6.6 10.8a15 15 0 0 0 6.6 6.6l2.2-2.2a1 1 0 0 1 1-.25 11.4 11.4 0 0 0 3.6.57 1 1 0 0 1 1 1V20a1 1 0 0 1-1 1A17 17 0 0 1 3 4a1 1 0 0 1 1-1h3.5a1 1 0 0 1 1 1c0 1.25.2 2.45.57 3.57a1 1 0 0 1-.25 1z"/></svg>
        555 0142 3380
      </span>
      <span class="contact-item">
        <svg viewBox="0 0 24 24" aria-hidden="true"><path d="M3 5h18v14H3z M3 5l9 7 9-7" fill="none" stroke="#fff" stroke-width="2"/></svg>
        mark@girderworks.com
      </span>
      <span class="contact-item">
        <svg viewBox="0 0 24 24" aria-hidden="true"><circle cx="12" cy="12" r="9" fill="none" stroke="#fff" stroke-width="2"/><path d="M3 12h18M12 3c3 3 3 15 0 18M12 3c-3 3-3 15 0 18" fill="none" stroke="#fff" stroke-width="1.5"/></svg>
        www.girderworks.com
      </span>
    </div>
  </section>
</main>
</body>
</html>
```